Upmarket Dessert Lounge needs a Business Card Design

We are an upmarket dessert lounge needing a business card to match our image.

We want something that is simple yet beautiful, feminine, classy, sophisticated and elegant. We want it to stand out and don't mind if it is bold.

The design should include our logo and colours of red or maroon with gold highlights. We don't mind if black is used.

Marlow & Quince

Target Market(s)

For those who like to indulge or treat themselves and give in to their temptations on good quality desserts.

Industry/Entity Type

Business

Requirements
Must have
• Must include our logo and our name

Marlow & Quince

M & Q

```html
<!DOCTYPE html>
<html lang="en">
<head>
<meta charset="utf-8">
<title>Marlow &amp; Quince — Business Card</title>
<link href="https://fonts.googleapis.com/css2?family=Source+Sans+3:wght@400;600&display=swap" rel="stylesheet">
<style>
  :root {
    --backdrop: #d9d9db;
    --card-black: #000000;
    --maroon: #7a1416;
    --cream: #fdd9a4;
    --gold: #f2c987;
    --white: #ffffff;
  }
  * { margin: 0; padding: 0; box-sizing: border-box; }
  html, body {
    width: 956px;
    height: 1200px;
    overflow: hidden;
    background: var(--backdrop);
    font-family: "Source Sans 3", "Myriad Pro", sans-serif;
  }
  .canvas { position: relative; width: 956px; height: 1200px; }

  .card {
    position: absolute;
    width: 798px;
    height: 457px;
    border-radius: 28px;
    background: var(--card-black);
    overflow: hidden;
    box-shadow: 0 6px 14px rgba(0,0,0,0.35);
  }
  .card--front { left: 79px; top: 71px; }
  .card--back { left: 73px; top: 632px; }

  .card__wave { position: absolute; left: 0; top: 0; width: 798px; height: 457px; }

  .brand-mark {
    position: absolute;
    color: var(--cream);
    font-weight: 400;
    white-space: nowrap;
    text-align: center;
  }
  .brand-mark--monogram {
    left: 64px; top: 120px; width: 308px;
    font-size: 78px; line-height: 1;
  }
  .brand-mark--name {
    left: 0; top: 200px; width: 798px;
    font-size: 46px; line-height: 1; letter-spacing: 1px;
  }

  .identity { position: absolute; left: 427px; top: 78px; color: var(--gold); font-size: 22px; line-height: 26px; }
  .identity__name { font-weight: 600; }
  .identity__role { font-weight: 400; letter-spacing: 0.5px; }

  .contact { position: absolute; left: 424px; color: var(--white); font-size: 19px; line-height: 30px; list-style: none; }
  .contact--numbers { top: 146px; }
  .contact--online { top: 242px; }
  .contact__label { font-weight: 600; }

  .address { position: absolute; left: 64px; top: 371px; color: var(--maroon); font-size: 19px; line-height: 26px; }
</style>
</head>
<body>
<main class="canvas">

  <section class="card card--front" aria-label="Business card front">
    <svg class="card__wave" viewBox="0 0 798 457" aria-hidden="true">
      <path d="M0 317 C 200 322, 420 360, 798 346 L798 457 L0 457 Z" fill="var(--cream)"/>
      <path d="M60 322 C 300 330, 560 420, 798 368 L798 420 C 560 448, 320 350, 60 322 Z" fill="var(--card-black)"/>
      <path d="M120 324 C 340 336, 560 412, 798 382 L798 400 C 560 430, 340 350, 120 324 Z" fill="var(--maroon)"/>
    </svg>

    <div class="brand-mark brand-mark--monogram">M &amp; Q</div>

    <div class="identity">
      <p class="identity__name">Your Name</p>
      <p class="identity__role">Designation</p>
    </div>

    <ul class="contact contact--numbers">
      <li><span class="contact__label">p</span> : 123-456-7890</li>
      <li><span class="contact__label">c</span> : 123-456-7890</li>
      <li><span class="contact__label">f</span> : 123-456-7890</li>
    </ul>
    <ul class="contact contact--online">
      <li><span class="contact__label">e</span> : name@yourwebsite.com</li>
      <li><span class="contact__label">w</span> : www.marlow&amp;quince.com</li>
    </ul>

    <address class="address" style="font-style: normal;">
      0000, Street Name<br>
      City Name, Country Code.
    </address>
  </section>

  <section class="card card--back" aria-label="Business card back">
    <div class="brand-mark brand-mark--name">MARLOW &amp; QUINCE</div>
  </section>

</main>
</body>
</html>
```